Ecological Cosmetics (w/ Social Impact) Website

Dr. Wendelin Marovitz Naturprodukte KELVORA®, a small family-run ecological cosmetics “start-up” business (has been around since the mid 90s but only now beginning professionalize management), wishes to redesign its web presence, as part of a comprehensive “facelift” that will also encompass at a later stage its corporate identity (e.g. logo…).
We would like to prepare a new trilingual (later 3 additional languages will be added) website (www.kelvora7.at) that is symbiotic with web 2.0 enabled interwoven with a blog, news section, social networks integrated (e.g. preference/like buttons, Facebook), changing images and announcements appearing on first page, online payment services, mobile internet compatibility (e.g. iOS, Android, BlackBerry… thus no use of Flash, no need for a specific app), etc. and all the other significant trends in the e-commerce realm. The website should be easily and quickly accessible, fun to navigate, allow us to update it simply (through a content manager) and so “sexy” that people will want to return to the web, inform themselves of events and news, and hopefully also try our products.
Our company is based in Austria and specializes in the production of organic cosmetics in the mid-upper pricing range. We pride ourselves in offering natural cosmetics (the meaning of “natural” is relative and each person may have a different definition), with no petrochemical preservatives. Some of our products, such as the mineral salts and black mud powder from the Dead Sea cannot be obtained more naturally, unless you actually visit the area, thus retain all their properties. Our products are not medicine but the basic Dead Sea ingredients are used by spas and clinics in the area to treat many different skin, joint and bone affections. Our male and female customers (no distinction made will be made on our new website), primarily as of the ages of 25 to 65, buy KELVORA® because they:
• Care about the exterior and interior well-being
• Wish to look well cared, preserve their skin’s flexibility, natural splendor & properties
• Prefer natural skin care
• Nourish their skin with vital minerals/trace elements, protecting/treating their skin with natural ingredients
• Willing to pay more than average for natural cosmetics, looking for quality,
• Don’t mind spending about 15 minutes per week preparing a mud mask with some hot water.
• Bathe in water enriched with mineral salts
• Know or are surprised to find out that Dead Sea mud is one of the few, if not the only, naturally astringent (tenses the skin) muds in the world
• Help alleviate skin conditions (e.g. psoriasis, dermatitis, acne, eczema, pustules, oily skin ...), joint (e.g. rheumatism, arthritis ...) and cardiovascular disease.
Amongst the minerals in many of our products (particularly salt, mud), are sulfur and zinc, two naturally disinfecting and healing minerals, thus their common use in many dermatological drugs. Both salt and mud powder are completely natural, and without chemicals additives, quite important when dealing with sensitive or problematic skin, which reacts allergically to certain types of substances. The KELVORA line blends in both ingredients, enriching them with the highest-quality vitamins, essential oils and exceptional plant oils. Many of the competitors creams today use common ingredients such as petrolatum, paraffin (paraffinum liquidum), mineral oil, among others, which are derived from oil, are cheap ingredients (higher margins!) and clog pores!
To underline that this is not a chimera, there are quite a few researchers/scientists/doctors who have written articles about the benefits of the Dead Sea and its naturally occurring substances. Below are some links to abstracts of research papers, which are helpful in understanding the therapeutic potential of the black mud powder and mineral salt:
http://onlinelibrary.wiley.com/doi/10.1111/j.1365-4362.1995.tb03599.x/abstract
http://onlinelibrary.wiley.com/doi/10.1111/j.1365-4632.2005.02079.x/full
http://onlinelibrary.wiley.com/doi/10.1046/j.1365-4362.1997.00204.x/abstract
http://ard.bmj.com/content/49/2/99.short
http://www.springerlink.com/content/pv46n2p1m9p3k131/
http://onlinelibrary.wiley.com/doi/10.1111/j.1365-4632.2005.02621.x/full
http://journals.lww.com/jclinrheum/Abstract/2002/08000/Therapy_With_Mud_Compresses_for_Knee.3.aspx
http://onlinelibrary.wiley.com/doi/10.1111/j.1468-3083.1997.tb00509.x/abstract
http://onlinelibrary.wiley.com/doi/10.1046/j.1529-8019.2003.01622.x/full
http://onlinelibrary.wiley.com/doi/10.1046/j.1365-4362.1999.00583.x/full
The following links lead you to KELVORA® product data, mineral characteristics and a video of how to prepare a facial mud mask:
http://www.kelvora7.at/descargaanalisis.htm
http://www.kelvora7.at/estudio.htm
http://www.clipverse.example/watch?v=Qm4TzLp8WxR
We would like to convey, through our striking and attractive new graphic design, our values to potential clients: quality, 100% natural product, effectiveness, seriousness, confidence, respect for the environment, people, animals (the products are not tested on animals), all of which has a price (they are not cheap!). To put our money where our mouth is and contribute to transforming our planet into a better place, we are discussing with NGOs donating a percentage of certain product sales to support their causes.
Our web currently is available in 3 languages: German, Spanish and English, however, we plan to expand it by another 2 to 3 languages (Portuguese, Russian, Chinese). We are looking for a graphic design that will communicate our values and captivate people's attention, thereby helping us increase sales, projecting a solid and elegant image of reliability, effectiveness, simplicity and trust. Although we are not, and do not wish to, market our products as medicine, we do want to express, through our new graphic design, the fact that these products can be used to treat all types of skin, mitigate certain skin affections (e.g. psoriasis, dermatitis, acne, eczema, sensitive skin), and, depending on each organism’s reaction, different ailments (e.g. arthritis, rheumatism), although they won’t cure them (they can alleviate!).
To get an idea of our company, I invite you to explore our website, www.kelvora7.at, and see photos of our products. Attached please find some photos of our products, including the newly designed black mud powder box. We would like to create a unified corporate image. At this point we know that some, if not all, packages do not convey quality nor our values – this is something we wish to gradually change as each products’ graphic design and packaging gets renewed, consistent with the new brand image. This is work-in-progress and will be addressed as the company grows and has the financial capacity to invest in new design and packaging. We are advancing step by step.
Content-wise, we would provide you with product photos, and the texts to be inserted, but would like to complement these with other photos (e.g. from photobanks that include images of the Dead Sea, beaches, plants, nature…). The design should quickly associate the Internet user/visitor of our website with our values and the idea of quality products. A content manager will be used to update and modify our product portfolio.
Although some people will find us by typing into their web browser the address of our website, many will use search engines to locate us on the WWW. For this purpose, it would also be important that kelvora7.at’s different webpages can be referenced, searched for keywords and allow analysis of webtraffic (e.g. Google Analytics…).
Two colors are being used in our packages, green Pantone No. 326 and blue Pantone No. 072. We are completely flexible in terms of colors.
We hope you find the project interesting. Any questions, please do not hesitate to contact us. Thank you very much for your time, recommendations and proposals. Ideally we can close this project in about 14 days.
Information to be considered and/or included in the design:
• The web will feature an e-commerce shop, whose design should also be included in your creative proposal.
• Cosmetics tend to be divided along the lines of skin types, yet as the KELVORA line is still quite small, we have decided to divide it along treatment areas: hair, face, body. Each product is indicated for a particular skin type.
• Keyword Search box for the entire website
The current web is slow, all in Flash, difficult to navigate, has too many intermediate stages, does not offer a keyword search function, nor incorporate any web 2.0 features. Furthermore, it is more difficult to find and index in search engines as none of the pages have specific web addresses. In terms of intermediate pages, these should be eliminated shortening the time the user needs to obtain the desired information (e.g. the landing page where you choose sex & language, followed by drop of water being filled up), such that the visitor is directly lead to the main page (equal to the landing page). At first glance, the blue background and the drop of water filling up may lead the visitor to believe we are dedicated to something with water, perhaps even plumbing or purification services – such an impression must be avoided. Perhaps one of the ways to analyze all the aspects to be incorporated is an evaluation of our current web’s weaknesses and prepare a design where those are all addressed.
Target Market(s)
Male & female customers, approx. age 18-65, who care about their exterior and interior well being, “worried” about their skin, willing to pay more tha
Industry/Entity Type
Graphic Design
Requirements
Must have
- • The web will also feature a blog and an e-commerce shop, whose designs should also be included in your creative proposal.
• Address current and future languages
Content-wise, we will product photos, and the texts to be inserted, but would like to complement these with other photos (e.g. from photobanks that include images of the Dead Sea, beaches, plants, nature…). The design should quickly associate the Internet user/visitor of our website with our values and the idea of quality products. A content manager will be used to update and modify our product portfolio, as well as effects announcements on the landing page.

```html
<!DOCTYPE html>
<html lang="en">
<head>
<meta charset="utf-8">
<title>Kelvora Naturprodukte</title>
<link rel="stylesheet" href="https://fonts.googleapis.com/css2?family=Source+Sans+3:wght@400;600;700&display=swap">
<style>
  :root {
    --sea-light: #3fa9e4;
    --sea-mid: #1f80cf;
    --sea-deep: #165fae;
    --frame: #1a5aa3;
    --navy: #13306a;
    --footer: #0c2062;
    --footer-link: #7390e2;
    --text-dark: #2a2a2a;
    --text-grey: #7a7a7a;
    --headline: #3f4448;
    --card-border: #d3d3d3;
    --white: #ffffff;
  }
  * { box-sizing: border-box; margin: 0; padding: 0; }
  html, body { width: 1200px; height: 1147px; overflow: hidden; }
  body {
    position: relative;
    background: var(--white);
    font-family: "Source Sans 3", "Myriad Pro", sans-serif;
  }
  .abs { position: absolute; }
  .nowrap { white-space: nowrap; }

  /* Header */
  .header-sea {
    left: 0; top: 0; width: 1200px; height: 545px;
    background:
      radial-gradient(ellipse 60% 30% at 30% 10%, rgba(120,210,255,.45), transparent 70%),
      radial-gradient(ellipse 50% 25% at 80% 20%, rgba(100,200,250,.35), transparent 70%),
      linear-gradient(180deg, var(--sea-light) 0%, var(--sea-mid) 25%, var(--sea-deep) 60%, var(--frame) 100%);
  }
  .util-links {
    left: 919px; top: 9px; width: 241px; height: 21px;
    border: 1px solid rgba(255,255,255,.55);
    border-radius: 11px;
    background: rgba(20,90,190,.55);
    color: var(--white);
    font-size: 12px;
    display: flex; align-items: center; justify-content: center;
    white-space: nowrap;
  }
  .lang-links { left: 1092px; top: 50px; color: #0d3f80; font-size: 11.5px; white-space: nowrap; }
  .brand { left: 62px; top: 22px; display: flex; align-items: center; gap: 12px; }
  .brand-dot { width: 112px; height: 112px; border-radius: 50%; background: var(--white); }
  .brand-name { color: var(--white); font-size: 26px; font-weight: 700; letter-spacing: .5px; }

  .main-nav {
    left: 416px; top: 110px; height: 29px;
    display: flex; align-items: center;
    font-size: 16px; color: #0f3a75; white-space: nowrap;
  }
  .main-nav a { color: inherit; text-decoration: none; padding: 0 19px; border-left: 1px solid rgba(255,255,255,.45); line-height: 18px; }
  .main-nav a:first-child, .main-nav a.active + a { border-left: none; }
  .main-nav a.active {
    background: var(--white); color: var(--navy);
    border-radius: 12px; line-height: 29px; padding: 0 20px;
    box-shadow: 0 1px 3px rgba(0,0,0,.25);
    margin-right: 2px;
  }

  .hero-frame {
    left: 39px; top: 164px; width: 1125px; height: 366px;
    background: var(--frame);
    box-shadow: inset 0 0 0 1px rgba(0,0,0,.15);
  }
  .hero-photo {
    left: 45px; top: 170px; width: 1113px; height: 354px;
    background:
      radial-gradient(ellipse 28% 55% at 22% 55%, #3fb6b0 0%, #2a9d9a 40%, transparent 75%),
      radial-gradient(ellipse 60% 70% at 70% 40%, #c9dfe0, transparent 80%),
      linear-gradient(120deg, #86b9bc 0%, #a9ccce 45%, #bcd6d8 70%, #8fb4b8 100%);
  }
  .hero-headline {
    left: 574px; top: 259px; width: 580px;
    font-size: 29px; line-height: 36px; color: var(--headline); white-space: nowrap;
  }
  .hero-headline strong { font-weight: 700; }
  .hero-headline span { font-weight: 400; font-size: 25px; }

  /* Category cards */
  .card {
    top: 564px; width: 355px; height: 189px;
    border: 1px solid var(--card-border); border-radius: 7px;
    background: linear-gradient(180deg, #ffffff 0%, #f3f3f3 55%, #dedede 100%);
    box-shadow: 0 1px 3px rgba(0,0,0,.15);
    overflow: hidden;
  }
  .card-photo {
    position: absolute; right: 0; top: 0; width: 140px; height: 100%;
    background: linear-gradient(90deg, rgba(230,230,230,0) 0%, #c99a7c 45%, #a8745a 100%);
  }
  .card-photo.hair { background: linear-gradient(90deg, rgba(230,230,230,0) 0%, #b99380 45%, #3a2d29 100%); }
  .card-title {
    position: absolute; left: 23px; top: 12px;
    font-size: 21px; font-weight: 700; color: var(--navy);
  }
  .card-text {
    position: absolute; left: 23px; top: 54px;
    font-size: 14.2px; line-height: 20.6px; color: var(--text-dark); white-space: nowrap;
  }

  /* Lower content */
  .section-title { font-size: 21px; font-weight: 700; color: var(--navy); }
  .welcome-text {
    left: 61px; top: 826px;
    font-size: 13.8px; line-height: 23px; color: var(--text-grey); white-space: nowrap;
  }
  .more { font-size: 13.5px; font-weight: 700; color: var(--navy); top: 980px; }
  .testimonial {
    left: 763px;
    font-size: 13.8px; line-height: 17.2px; color: var(--text-dark); white-space: nowrap;
  }
  .dash { left: 763px; width: 370px; border-top: 1px dashed #a9a9a9; }

  /* Footer */
  .site-footer { left: 0; top: 1021px; width: 1200px; height: 126px; background: var(--footer); }
  .footer-nav { left: 0; top: 1049px; width: 700px; height: 16px; font-size: 11.5px; color: var(--footer-link); }
  .footer-nav span { position: absolute; top: 0; white-space: nowrap; }
  .copyright { left: 58px; top: 1087px; font-size: 10px; line-height: 15.5px; color: var(--white); white-space: nowrap; }
  .social { left: 998px; top: 1077px; display: flex; gap: 9px; }
  .social i { display: block; width: 21px; height: 21px; border-radius: 50%; }
</style>
</head>
<body>
  <div class="abs header-sea" role="img" aria-label="Sea water surface background"></div>

  <div class="abs util-links">Sitemap | Links | Downloads | Contacts</div>
  <div class="abs lang-links">En | De | Es</div>

  <div class="abs brand">
    <div class="brand-dot"></div>
    <div class="brand-name">KELVORA®</div>
  </div>

  <nav class="abs main-nav">
    <a class="active">Kelvora</a>
    <a>Dead Sea</a>
    <a>Aromatherapy</a>
    <a>Facial Care</a>
    <a>Body Care</a>
    <a>Hair Care</a>
    <a>Spas</a>
  </nav>

  <div class="abs hero-frame"></div>
  <div class="abs hero-photo" role="img" aria-label="Turquoise cream jar resting on Dead Sea salt crystals"></div>
  <p class="abs hero-headline"><strong>Lorem Ipsum is simply dummy text of the</strong><br><strong>printing</strong> <span>and typesetting industry.</span></p>

  <article class="abs card" style="left:39px">
    <div class="card-photo" role="img" aria-label="Smiling man with face cream on his cheek"></div>
    <h2 class="card-title">Facial Care</h2>
    <p class="card-text">Lorem Ipsum is simply dummy<br>text of the printing and<br>typesetting industry. Lorem<br>Ipsum has been the industry's<br>standard dummy</p>
  </article>
  <article class="abs card" style="left:422px">
    <div class="card-photo" role="img" aria-label="Bare male torso"></div>
    <h2 class="card-title" style="left:28px">Body Care</h2>
    <p class="card-text" style="left:25px">Lorem Ipsum is simply dummy<br>text of the printing and<br>typesetting industry. Lorem<br>Ipsum has been the industry's<br>standard dummy</p>
  </article>
  <article class="abs card" style="left:808px">
    <div class="card-photo hair" role="img" aria-label="Man with dark tousled hair"></div>
    <h2 class="card-title">Hair Care</h2>
    <p class="card-text">Lorem Ipsum is simply<br>dummy text of the printing<br>and typesetting industry.<br>Lorem Ipsum has been the<br>industry's standard dummy</p>
  </article>

  <h2 class="abs section-title" style="left:57px; top:788px">Welcome to Kelvora</h2>
  <p class="abs welcome-text">Lorem Ipsum is simply dummy text of the printing and typesetting industry. Lorem Ipsum has been<br>the industry's standard dummy text ever since the 1500s, when an unknown printer took a galley of<br>type and scrambled it to make a type specimen book. It has survived not only five centuries, but also<br>the leap into electronic typesetting, remaining essentially unchanged. It was popularised in the<br>1960s with the release of Dravenset sheets containing Lorem Ipsum passages, and more recently with<br>desktop publishing software like Orlin PageCraft including versions of Lorem Ipsum.</p>
  <a class="abs more" style="left:660px">more</a>

  <h2 class="abs section-title" style="left:762px; top:788px">Testimonials</h2>
  <p class="abs testimonial" style="top:827px">Lorem Ipsum is simply dummy text of the printing and<br>typesetting industry. Lorem Ipsum has been the industry's<br>standard dummy</p>
  <div class="abs dash" style="top:888px"></div>
  <p class="abs testimonial" style="top:900px">Lorem Ipsum is simply dummy text of the printing and<br>typesetting industry. Lorem Ipsum has been the industry's<br>standard dummy</p>
  <div class="abs dash" style="top:961px"></div>
  <a class="abs more" style="left:1097px">more</a>

  <footer class="abs site-footer"></footer>
  <div class="abs footer-nav">
    <span style="left:56px">Kelvora</span>
    <span style="left:116px">Dead Sea</span>
    <span style="left:194px">Aromatherapy</span>
    <span style="left:300px">Facial Care</span>
    <span style="left:387px">Body Care</span>
    <span style="left:469px">Hair Care</span>
    <span style="left:546px">Spas</span>
  </div>
  <p class="abs copyright">Copyright ©2012<br>by KELVORA NATURPRODUKTE DR. WENDELIN MAROVITZ.<br>All rights reserved.</p>
  <div class="abs social" aria-label="Social network links">
    <i style="background:#1a8fd8"></i>
    <i style="background:#4a66a8"></i>
    <i style="background:#d9d9e6"></i>
    <i style="background:#3aa3cf"></i>
    <i style="background:#ee7a1e"></i>
  </div>
</body>
</html>
```